Veldmark Supplies Business Card

Professional business card that stand out to our potential customers. Front and back with clean modern design

Industry/Entity Type

Oil and gas

Contact Information for Business Card

Name, address, website , office phone and cell number

Requirements
Must have
• Editable files for each employee

```html
<!DOCTYPE html>
<html lang="en">
<head>
<meta charset="utf-8">
<title>Veldmark Supplies Business Card</title>
<link rel="stylesheet" href="https://fonts.googleapis.com/css2?family=Montserrat:wght@400;500;700;800&display=swap">
<style>
  :root {
    --stage: #2e2f31;
    --paper: #f1f1f1;
    --red: #e01f26;
    --blue: #0ea2c7;
    --ink: #1b1b1b;
  }
  * { margin: 0; padding: 0; box-sizing: border-box; }
  html, body { width: 1200px; height: 1059px; overflow: hidden; }
  body {
    background: var(--stage);
    font-family: "Montserrat", Arial, sans-serif;
    color: var(--ink);
    position: relative;
  }
  .card {
    position: absolute;
    background: var(--paper);
    border-radius: 24px;
  }
  .card-front { left: 256px; top: 100px; width: 688px; height: 393px; }
  .card-back  { left: 253px; top: 536px; width: 694px; height: 397px; }

  .brand { position: absolute; left: 0; right: 0; text-align: center; }
  .brand-square { display: block; margin: 0 auto; background: var(--red); }
  .brand-name {
    display: block;
    font-weight: 800;
    color: var(--red);
    text-transform: uppercase;
    letter-spacing: 0.02em;
    white-space: nowrap;
  }
  .card-front .brand { top: 30px; }
  .card-front .brand-square { width: 74px; height: 74px; }
  .card-front .brand-name { margin-top: 42px; font-size: 19px; }

  .person {
    position: absolute;
    right: 375px;
    top: 240px;
    text-align: right;
  }
  .person-name {
    font-size: 33px;
    font-weight: 700;
    line-height: 1;
    white-space: nowrap;
  }
  .person-name .first { color: var(--red); }
  .person-name .last { color: var(--blue); }
  .person-title {
    margin-top: 12px;
    font-size: 17px;
    font-weight: 500;
  }

  .divider {
    position: absolute;
    left: 341px;
    top: 222px;
    width: 2px;
    height: 98px;
    background: var(--red);
  }

  .contacts {
    position: absolute;
    left: 368px;
    top: 221px;
    list-style: none;
  }
  .contacts li {
    display: flex;
    align-items: center;
    height: 27px;
    font-size: 17.5px;
    white-space: nowrap;
  }
  .contacts svg { width: 15px; height: 15px; margin-right: 10px; flex: none; fill: var(--red); }

  .address {
    position: absolute;
    left: 0; right: 0;
    top: 350px;
    text-align: center;
    font-size: 17px;
    font-weight: 500;
  }

  .card-back .brand { top: 58px; }
  .card-back .brand-square { width: 150px; height: 150px; }
  .card-back .brand-name { margin-top: 82px; font-size: 38px; }
</style>
</head>
<body>

<section class="card card-front" aria-label="Card front">
  <div class="brand">
    <span class="brand-square"></span>
    <span class="brand-name">Veldmark Supplies</span>
  </div>

  <div class="person">
    <p class="person-name"><span class="first">DANIEL</span> <span class="last">MARSH</span></p>
    <p class="person-title">Managing Director</p>
  </div>

  <div class="divider"></div>

  <ul class="contacts">
    <li>
      <svg viewBox="0 0 16 16" aria-hidden="true"><path d="M1 6c0-2 3-4 7-4s7 2 7 4v1h-4V5.5H5V7H1zM3 8h10l1 6H2z"/></svg>
      (555)210-0387
    </li>
    <li>
      <svg viewBox="0 0 16 16" aria-hidden="true"><path d="M4 0h8a1 1 0 0 1 1 1v14a1 1 0 0 1-1 1H4a1 1 0 0 1-1-1V1a1 1 0 0 1 1-1zm1 2v10h6V2zm3 11a1 1 0 1 0 0 2 1 1 0 0 0 0-2z"/></svg>
      555 013 472
    </li>
    <li>
      <svg viewBox="0 0 16 16" aria-hidden="true"><path d="M0 3h16v10H0zm2 1.5 6 4.5 6-4.5V4H2zM2 6.5V12h12V6.5L8 11z"/></svg>
      sales@veldmarksupplies.com
    </li>
    <li>
      <svg viewBox="0 0 16 16" aria-hidden="true"><path d="M8 0a8 8 0 1 0 0 16A8 8 0 0 0 8 0zM3 5l3 1 1 3-2 1-1 3a6 6 0 0 1-1-8zm7-3 1 2-2 2 3 1 1 3 1-1a6 6 0 0 0-4-7z"/></svg>
      www.veldmarksupplies.com
    </li>
  </ul>

  <p class="address">417 N.Larkfield Suite 5 Midland, Tx 79701</p>
</section>

<section class="card card-back" aria-label="Card back">
  <div class="brand">
    <span class="brand-square"></span>
    <span class="brand-name">Veldmark Supplies</span>
  </div>
</section>

</body>
</html>
```